Vosley Insurance Stationery Design Project

We need a stationery design for business cards, letterhead and envelopes.

Please refer to attached brief for further information.

Industry/Entity Type

Business

```html
<!DOCTYPE html>
<html lang="en">
<head>
<meta charset="utf-8">
<title>Vosley Insurance – Business Card</title>
<link rel="stylesheet" href="https://fonts.googleapis.com/css2?family=Open+Sans:wght@400;600;700&display=swap">
<style>
  :root {
    --backdrop: #b38a2a;
    --card-white: #ffffff;
    --card-grey: #cccccc;
    --orange: #f47521;
    --ink: #333333;
    --muted: #666666;
    --band: #c4c4c4;
  }
  * { box-sizing: border-box; margin: 0; padding: 0; }
  html, body { width: 1200px; height: 686px; overflow: hidden; }
  body {
    position: relative;
    background: var(--backdrop);
    font-family: "Open Sans", sans-serif;
  }
  .card {
    position: absolute;
    width: 524px;
    height: 298px;
    box-shadow: 2px 2px 4px rgba(0,0,0,0.45);
  }
  .card-front { left: 55px; top: 157px; background: var(--card-white); }
  .card-back  { left: 612px; top: 241px; background: var(--card-grey); }

  .brand { position: absolute; display: flex; align-items: center; }
  .brand-dot { border-radius: 50%; background: var(--orange); flex: none; }
  .brand-name { color: var(--orange); font-weight: 700; }

  .card-front .brand { left: 28px; top: 38px; }
  .card-front .brand-dot { width: 17px; height: 17px; margin-right: 10px; }
  .card-front .brand-name { font-size: 26px; line-height: 1; }

  .holder { position: absolute; right: 16px; top: 35px; text-align: right; }
  .holder-name { color: var(--orange); font-weight: 700; font-size: 15.5px; line-height: 1.2; }
  .holder-role { color: var(--muted); font-weight: 700; font-size: 11px; margin-top: 2px; }

  .address {
    position: absolute; left: 33px; top: 118px;
    font-size: 11.5px; line-height: 15.5px; color: var(--ink);
    font-style: normal;
  }
  .contacts {
    position: absolute; left: 33px; top: 186px;
    list-style: none; font-size: 11.5px; line-height: 18px; color: var(--ink);
  }
  .contacts b { color: var(--orange); font-weight: 700; }

  .disclosure {
    position: absolute; right: 16px; top: 151px;
    text-align: right; font-size: 11px; line-height: 17px; color: var(--muted);
  }
  .tagline {
    position: absolute; left: 27px; top: 269px;
    width: 354px; height: 18px; padding-left: 7px;
    background: var(--band); color: #ffffff;
    font-weight: 700; font-size: 13px; line-height: 18px;
  }

  .card-back .brand { left: 25px; top: 102px; }
  .card-back .brand-dot { width: 40px; height: 40px; margin-right: 12px; align-self: flex-start; }
  .card-back .brand-name { font-size: 29px; line-height: 1.05; }
  .website {
    position: absolute; left: 234px; top: 132px;
    color: var(--orange); font-weight: 700; font-size: 15.5px;
  }
</style>
</head>
<body>
  <section class="card card-front">
    <div class="brand">
      <span class="brand-dot"></span>
      <span class="brand-name">Vosley Insurance</span>
    </div>
    <div class="holder">
      <p class="holder-name">Dan Hartley</p>
      <p class="holder-role">Director</p>
    </div>
    <address class="address">
      Level 4, 18 Carrow St.<br>
      Eastbrook NSW 2071<br>
      PO Box 418<br>
      Eastbrook NSW 2070
    </address>
    <ul class="contacts">
      <li><b>T</b> : (02) 5550 1234</li>
      <li><b>F</b> : (02) 5550 7812</li>
      <li><b>M</b> : 0400 555 219</li>
      <li><b>E</b> : dhartley@vosley.com.au</li>
    </ul>
    <p class="disclosure">
      Authorised Representative No. 400128<br>
      Harbourline Advisory Australia Pty Limited<br>
      AFSL 550311 Harbourline Financial Services<br>
      Pty Ltd and its advisers are members of Carrick<br>
      Financial Advisers and Authorised Representatives<br>
      of Westmere Advice group Pty Ltd AFSL 550742
    </p>
    <p class="tagline">Business and Life Insurance Brokers and Advisers</p>
  </section>

  <section class="card card-back">
    <div class="brand">
      <span class="brand-dot"></span>
      <span class="brand-name">Vosley<br>Insurance</span>
    </div>
    <p class="website">www.vosleyinsurance.com.au</p>
  </section>
</body>
</html>
```